Advertising company unique advertising platform

we need a logo design for a new company based in Australia Melbourne. We develop innovated advertising platform where consumer can use this platform to get regular discount, as business owner they can use this platform for free advertisement. Payment for this advertisement platform only payable every two weeks, when I generate revenue for their business

Industry/Entity Type

Advertising

Contact Information for Business Card

Dale Morven | Co-Founder |Managing Director
Suite 718 240 Wattlebrook Lane Melbourne Vic 3000

ABN 38 614 207 923
Tel: +61 0487 259 318 | Email: dale.morven@plivorantu.com

Font styles to use
Decorative
Script

Requirements
Must have
• Try few different design and some round corner business card
Should not have
• One round corner business card...try 4 different colour background not only black, make sure two side is designed. Be creative so imagine you are giving this to a client make sure has wow factor, if you can also try one design with engrave like all the logo, words look 3d feel
• The word Advertising Platform use attached file font

```html
<!DOCTYPE html>
<html lang="en">
<head>
<meta charset="utf-8">
<title>Kestrine Exchange – Business Card</title>
<link rel="stylesheet" href="https://fonts.googleapis.com/css2?family=Open+Sans:wght@400;600;700&display=swap">
<style>
  :root {
    --backdrop: #d9d9db;
    --card: #232323;
    --card-edge: #2e2e2e;
    --text-light: #e9e9e9;
    --text-dark: #1d1d1d;
    --brand: #f07a2a;
    --band-red: #ea4a2c;
    --band-orange: #f5902e;
    --band-yellow: #f6c548;
    --wave-cyan: #35c6e6;
    --wave-blue: #3a73c8;
    --icon-red: #e2452e;
  }
  * { margin: 0; padding: 0; box-sizing: border-box; }
  html, body { width: 1200px; height: 840px; overflow: hidden; }
  body {
    background: var(--backdrop);
    font-family: "Open Sans", Arial, sans-serif;
    position: relative;
  }
  .card {
    position: absolute;
    width: 580px;
    height: 354px;
    border-radius: 22px;
    background: var(--card);
    overflow: hidden;
    box-shadow: 0 10px 28px rgba(0,0,0,0.22);
  }
  .card--back { left: 90px; top: 50px; }
  .card--front { left: 530px; top: 436px; }

  .brand {
    display: flex;
    align-items: center;
    gap: 12px;
    color: var(--brand);
    font-weight: 700;
    line-height: 1.05;
  }
  .brand__dot {
    border-radius: 50%;
    background: var(--brand);
    flex: none;
  }
  .card--back .brand {
    position: absolute;
    left: 50%; top: 50%;
    transform: translate(-50%, -50%);
    font-size: 34px;
  }
  .card--back .brand__dot { width: 46px; height: 46px; }

  .card--front .brand {
    position: absolute;
    left: 40px; top: 48px;
    font-size: 24px;
  }
  .card--front .brand__dot { width: 36px; height: 36px; }

  .wave-band { position: absolute; left: 0; top: 0; width: 580px; height: 354px; }

  .holder {
    position: absolute;
    right: 26px; top: 112px;
    text-align: right;
    color: var(--text-dark);
    font-size: 15px;
    line-height: 1.2;
    text-transform: uppercase;
  }
  .holder__name { font-weight: 700; }

  .contact {
    position: absolute;
    left: 40px; top: 150px;
    color: var(--text-light);
    font-size: 13px;
    line-height: 1.55;
    list-style: none;
  }
  .contact li { display: flex; align-items: center; gap: 7px; }
  .contact svg { width: 12px; height: 12px; flex: none; }

  .address {
    position: absolute;
    right: 30px; bottom: 30px;
    text-align: right;
    color: var(--text-light);
    font-size: 15px;
    line-height: 1.35;
  }
</style>
</head>
<body>

  <section class="card card--back" aria-label="Business card, back">
    <div class="brand">
      <span class="brand__dot"></span>
      <span class="brand__name">Kestrine<br>Exchange</span>
    </div>
  </section>

  <section class="card card--front" aria-label="Business card, front">
    <svg class="wave-band" viewBox="0 0 580 354" aria-hidden="true">
      <defs>
        <linearGradient id="bandFill" x1="0" y1="0" x2="1" y2="0.4">
          <stop offset="0" stop-color="var(--band-red)"/>
          <stop offset="0.45" stop-color="var(--band-yellow)"/>
          <stop offset="0.75" stop-color="var(--band-orange)"/>
          <stop offset="1" stop-color="var(--band-red)"/>
        </linearGradient>
        <linearGradient id="waveLine" x1="0" y1="0" x2="1" y2="0">
          <stop offset="0" stop-color="var(--wave-cyan)"/>
          <stop offset="0.6" stop-color="var(--wave-blue)"/>
          <stop offset="1" stop-color="var(--wave-cyan)"/>
        </linearGradient>
      </defs>
      <path d="M60,0 C200,28 250,130 360,170 C450,202 520,214 580,222 L580,0 Z" fill="url(#bandFill)"/>
      <path d="M60,4 C200,34 250,138 360,178 C450,210 520,222 580,230" fill="none" stroke="url(#waveLine)" stroke-width="5"/>
    </svg>

    <div class="brand">
      <span class="brand__dot"></span>
      <span class="brand__name">Kestrine<br>Exchange</span>
    </div>

    <div class="holder">
      <div class="holder__name">Dale Morven</div>
      <div>Co-Founder</div>
      <div>Managing Director</div>
    </div>

    <ul class="contact">
      <li>Plivorantu</li>
      <li>ABN 38 614 207 923</li>
      <li>
        <svg viewBox="0 0 12 12" aria-label="Phone"><path fill="var(--icon-red)" d="M2.5 1h2l1 2.5-1.3.9a6 6 0 0 0 3.4 3.4l.9-1.3L11 7.5v2A1.5 1.5 0 0 1 9.5 11 8.5 8.5 0 0 1 1 2.5 1.5 1.5 0 0 1 2.5 1z"/></svg>
        +61 0487 259 318
      </li>
      <li>
        <svg viewBox="0 0 12 12" aria-label="Email"><rect x="0.5" y="2" width="11" height="8" rx="1" fill="var(--icon-red)"/><path d="M1 2.6 6 6.6l5-4" fill="none" stroke="var(--card)" stroke-width="1"/></svg>
        dale.morven@plivorantu.com
      </li>
    </ul>

    <address class="address" style="font-style:normal">
      Suite 718 240<br>
      Wattlebrook Lane<br>
      Melbourne Vic 3000
    </address>
  </section>

</body>
</html>
```